Visitenkarten-Design für Sonnen-/Fensterschutz
Zielgruppe
KLW GmbH ist eine Firma, die Sonnenschutz und Fensterschutz anbieten.
'Ihr kompetenter Partner in Sachen Sonnenschutz- , Fenster- und Türtechnik. Sie erhalten echtes Handwerk aus dem Mühlviertel zu fairen Preisen.'
Unsere Zielgruppe sind Personen mit Haus, die am Land leben.
Firmenname: KLW GmbH
Slogan: Fenster & Sonnenschutz
Aufgabenstellung
Hier befindet sich das Logodesign: https://dx.qv/t-QwLpo7RbNs
Bitte ein schlichtes Design bereitstellen mit einer Dummy-Person:
Jonas Weidlinger + Telefonnummer + Email
Die finalen Daten bitte erst am Schluss berücksichtigen (für Gewinnerdesign)
Gerne auch hintern + vorne bedruckbar bereitstellen.

```html
<!DOCTYPE html>
<html lang="de">
<head>
<meta charset="utf-8">
<title>KLW GmbH – Visitenkarte</title>
<link rel="stylesheet" href="https://fonts.googleapis.com/css2?family=Arimo:wght@400;700&display=swap">
<style>
  :root {
    --bg: #e4e4e4;
    --card: #ffffff;
    --red: #d9363a;
    --orange: #e5762f;
    --ink: #4a4a4a;
    --ink-soft: #5c5c5c;
    --bar: #555555;
  }
  * { box-sizing: border-box; margin: 0; padding: 0; }
  html, body { width: 1200px; height: 842px; overflow: hidden; }
  body {
    background: var(--bg);
    font-family: "Arimo", Arial, sans-serif;
    position: relative;
  }
  .card {
    position: absolute;
    top: 253px;
    width: 520px;
    height: 336px;
    background: var(--card);
    box-shadow: 0 2px 8px rgba(0,0,0,0.12);
    overflow: hidden;
  }
  .card--front { left: 60px; }
  .card--back { left: 620px; }

  /* Vorderseite */
  .brand-band {
    position: absolute;
    left: 0; right: 0;
    top: 96px;
    height: 86px;
    background: linear-gradient(90deg, var(--red), var(--orange));
  }
  .brand-band .wordmark {
    position: absolute;
    left: 60px;
    top: 22px;
    display: flex;
    align-items: center;
    gap: 12px;
    color: #ffffff;
    font-weight: 700;
    font-size: 38px;
    letter-spacing: 1px;
  }
  .wordmark .mark-square {
    width: 26px; height: 26px;
    background: currentColor;
  }
  .front-slogan {
    position: absolute;
    left: 60px;
    top: 192px;
    color: var(--red);
    font-size: 14px;
    letter-spacing: 1.5px;
    text-transform: uppercase;
  }

  /* Rückseite */
  .divider {
    position: absolute;
    left: 330px;
    width: 14px;
    background: var(--bar);
  }
  .divider--top { top: 0; height: 70px; }
  .divider--bottom { top: 162px; bottom: 0; }
  .back-brand {
    position: absolute;
    left: 250px;
    top: 86px;
    background: var(--card);
    padding: 4px 8px;
  }
  .back-brand .wordmark {
    display: flex;
    align-items: center;
    gap: 10px;
    color: var(--orange);
    font-weight: 700;
    font-size: 30px;
    letter-spacing: 1px;
  }
  .back-brand .mark-square {
    width: 20px; height: 20px;
    background: currentColor;
  }
  .back-brand .slogan {
    margin-top: 4px;
    color: var(--red);
    font-size: 11px;
    letter-spacing: 1.2px;
    text-transform: uppercase;
  }
  .contact {
    position: absolute;
    left: 42px;
    top: 150px;
    color: var(--ink);
  }
  .contact .name { font-weight: 700; font-size: 19px; letter-spacing: 0.5px; }
  .contact .role { font-size: 13px; color: var(--ink-soft); margin-bottom: 12px; }
  .contact h3 { font-size: 12px; font-weight: 700; margin-bottom: 1px; }
  .contact dl {
    display: grid;
    grid-template-columns: 50px auto;
    font-size: 12px;
    line-height: 15px;
    color: var(--ink-soft);
    margin-bottom: 10px;
  }
  .contact address {
    font-style: normal;
    font-size: 12px;
    line-height: 15px;
    color: var(--ink-soft);
  }
</style>
</head>
<body>
  <section class="card card--front" aria-label="Vorderseite">
    <div class="brand-band">
      <div class="wordmark"><span class="mark-square"></span>KLW GmbH</div>
    </div>
    <p class="front-slogan">Fenster &amp; Sonnenschutz</p>
  </section>

  <section class="card card--back" aria-label="Rückseite">
    <div class="divider divider--top"></div>
    <div class="divider divider--bottom"></div>
    <div class="back-brand">
      <div class="wordmark"><span class="mark-square"></span>KLW GmbH</div>
      <p class="slogan">Fenster &amp; Sonnenschutz</p>
    </div>
    <div class="contact">
      <p class="name">Tobias Renner</p>
      <p class="role">Geschäftsführer</p>
      <h3>Kontakt</h3>
      <dl>
        <dt>Tel</dt><dd>+49 0000 000 39</dd>
        <dt>Fax</dt><dd>+49 0000 000 00</dd>
        <dt>Mobil</dt><dd>+49 0000 000 39</dd>
        <dt>E-mail</dt><dd>tr@klw-fenster.de</dd>
      </dl>
      <h3>Anschrift</h3>
      <address>KLW GmbH Am Lindenhang 12-14<br>41236 Feldbrück</address>
    </div>
  </section>
</body>
</html>
```